Flyer for corporate discount for dog daycare

I own a dog daycare with a large corporate down the road. I am working with the President of the company to offer their employees a discount for my services, Dog Daycare, Overnight Care, Grooming Salon & Spa and Retail. The design should be professional but also have a soft side as people view their dogs similar to human children.

I attached my logo along with our grooming brochure for reference on colors we've been using.

At a minimum the flyer must contain the following information:
Name: The Maple Kennel
web address: www.TailbrookLodge.example
phone number: 555-314-8860
Address: 4870 Larchmont Lane
Google Map of our location

Title of flyer/program: Corporate V.I.P. (Very Important Pooch) (Can be creative with how to include this such as, Welcome to our Corporate. . .. etc.)

The program offer is: 5% discount
My services: Dog Daycare, Overnight Care, Grooming Salon & Spa and Retail

Target Market(s)

corporate employees, male and female, age 24+

Requirements
Must have
• Must be easy to read and inviting.
Nice to have
• Nice photo dogs playing or inviting photo of dog.
Should not have
• cartoon feel

```html
<!DOCTYPE html>
<html lang="en">
<head>
<meta charset="utf-8">
<title>The Maple Kennel – Corporate V.I.P Flyer</title>
<link href="https://fonts.googleapis.com/css2?family=Raleway:wght@300;400;600;700;800&family=Montserrat:wght@700;800;900&family=Pacifico&display=swap" rel="stylesheet">
<style>
  :root {
    --backdrop: #5f9499;
    --paper: #f4f4f3;
    --teal-light: #a9d9df;
    --teal-mid: #5cb3bc;
    --teal-deep: #3f8e97;
    --brown: #4d4331;
    --brown-dark: #3a3225;
    --taupe: #8a8070;
    --white: #ffffff;
  }
  * { margin: 0; padding: 0; box-sizing: border-box; }
  html, body { width: 1200px; height: 1159px; overflow: hidden; }
  body { background: var(--backdrop); font-family: "Raleway", sans-serif; }

  .flyer {
    position: absolute; left: 225px; top: 28px;
    width: 750px; height: 1103px;
    background: linear-gradient(180deg, var(--paper) 60%, var(--white) 100%);
    overflow: hidden;
    box-shadow: 0 6px 24px rgba(0,0,0,.25);
  }
  .flyer > * { position: absolute; white-space: nowrap; }

  .header-photo {
    left: 0; top: 0; width: 750px; height: 300px;
    background: linear-gradient(100deg, #cfc9c2 0%, #b9b1a8 40%, #a8a098 60%, #c9b8bd 85%, #bfb6b0 100%);
  }
  .shapes { left: 0; top: 0; width: 750px; height: 1103px; }

  .brand { left: 60px; top: 55px; width: 280px; text-align: center; }
  .brand-mark { width: 86px; height: 86px; margin: 0 auto 12px; background: var(--teal-light); }
  .brand-name { font-weight: 600; font-size: 27px; color: var(--brown); letter-spacing: .5px; }

  .services {
    right: 34px; top: 48px; text-align: right;
    color: var(--white); font-weight: 700; font-size: 23px; line-height: 32px;
  }
  .services .more { font-size: 18px; font-weight: 600; }

  .tagline {
    left: 300px; top: 226px; width: 450px; text-align: center;
    font-weight: 800; font-size: 29px; color: var(--white);
  }
  .tagline .soft { color: var(--teal-light); font-weight: 700; }

  .dog-photo {
    left: 55px; top: 232px; width: 290px; height: 590px;
    background: radial-gradient(ellipse at 50% 40%, #c9874f 0%, #a96a3a 45%, #7a4a28 75%, rgba(122,74,40,0) 100%);
    border-radius: 45% 45% 20% 20%;
  }

  .program-kicker {
    left: 350px; top: 300px; width: 380px; text-align: center;
    font-weight: 300; font-size: 56px; color: var(--taupe); letter-spacing: 1px;
  }
  .program-title {
    left: 345px; top: 355px; width: 390px; text-align: center;
    font-family: "Montserrat", sans-serif; font-weight: 800; font-size: 150px;
    line-height: 1; color: var(--brown); letter-spacing: -3px;
  }
  .program-sub {
    left: 350px; top: 515px; width: 380px; text-align: center;
    font-weight: 700; font-size: 28px; color: var(--taupe);
  }

  .offer-figure {
    left: 400px; top: 575px; width: 340px; text-align: center;
    font-family: "Montserrat", sans-serif; font-weight: 900; font-size: 180px; line-height: 1;
    color: var(--teal-mid);
    text-shadow: -2px -2px 0 var(--brown-dark), 2px -2px 0 var(--brown-dark), -2px 2px 0 var(--brown-dark),
                 2px 2px 0 var(--brown-dark), 6px 6px 0 var(--teal-deep), 9px 9px 0 var(--brown-dark);
  }
  .offer-label {
    left: 400px; top: 772px; width: 345px; text-align: center;
    font-family: "Montserrat", sans-serif; font-weight: 900; font-size: 46px; line-height: 1;
    color: var(--teal-mid);
    text-shadow: -2px -2px 0 var(--brown-dark), 2px -2px 0 var(--brown-dark), -2px 2px 0 var(--brown-dark),
                 2px 2px 0 var(--brown-dark), 4px 4px 0 var(--brown-dark);
  }

  .location-map {
    left: 423px; top: 842px; width: 318px; height: 140px;
    background: linear-gradient(160deg, #eceae6 0%, #e2ded7 55%, #f1dcc4 80%, #cfe3ee 100%);
    border: 5px solid var(--brown-dark);
  }

  .contact-cta {
    left: 40px; top: 757px; width: 212px; height: 212px; border-radius: 50%;
    background: var(--teal-deep); color: var(--white);
    font-family: "Pacifico", cursive; font-size: 38px; line-height: 52px;
    display: flex; flex-direction: column; align-items: center; justify-content: center;
    transform: rotate(-8deg);
  }

  .website {
    left: 40px; top: 1040px; font-weight: 800; font-size: 28px; color: var(--brown-dark);
  }
  .contact-list { left: 430px; top: 998px; color: var(--brown-dark); font-weight: 700; font-size: 23px; }
  .contact-item { display: flex; align-items: center; gap: 12px; height: 44px; }
  .contact-item svg { width: 26px; height: 30px; flex: none; }
</style>
</head>
<body>
  <main class="flyer">
    <div class="header-photo" role="img" aria-label="Soft blurred photo of dogs in the daycare"></div>

    <svg class="shapes" viewBox="0 0 750 1103" aria-hidden="true">
      <polygon points="0,290 750,240 750,560 0,600" fill="var(--teal-light)" opacity=".9"/>
      <polygon points="285,218 750,208 750,258 285,262" fill="var(--brown)"/>
      <polygon points="150,812 423,800 423,860 150,870" fill="var(--brown)" opacity=".75"/>
      <polygon points="216,930 244,968 200,950" fill="var(--teal-deep)"/>
    </svg>

    <div class="brand">
      <div class="brand-mark"></div>
      <div class="brand-name">The Maple Kennel</div>
    </div>

    <div class="services">
      Dog Daycare<br>Overnight Care<br>Grooming Salon &amp; Spa<br><span class="more">and more...</span>
    </div>

    <div class="tagline">YOUR POOCH <span class="soft">joined yet?</span></div>

    <div class="dog-photo" role="img" aria-label="Photo of a boxer dog sitting and looking at the viewer"></div>

    <div class="program-kicker">CORPORATE</div>
    <div class="program-title">V.I.P</div>
    <div class="program-sub">Very Important Pooch</div>

    <div class="offer-figure">5%</div>
    <div class="offer-label">DISCOUNT</div>

    <div class="location-map" role="img" aria-label="Street map showing the kennel location"></div>

    <div class="contact-cta"><span>Get in</span><span>touch</span></div>

    <div class="website">TailbrookLodge.example</div>

    <div class="contact-list">
      <div class="contact-item">
        <svg viewBox="0 0 28 32"><path d="M14 2a10 10 0 0 0-10 10c0 7 10 18 10 18s10-11 10-18A10 10 0 0 0 14 2z" fill="none" stroke="var(--teal-mid)" stroke-width="3"/><circle cx="14" cy="12" r="3.5" fill="var(--teal-mid)"/></svg>
        <span>4870 Larchmont Lane</span>
      </div>
      <div class="contact-item">
        <svg viewBox="0 0 28 32"><path d="M3 12c0-4 5-6 11-6s11 2 11 6l-4 2-3-3h-8l-3 3z" fill="var(--teal-mid)"/><rect x="6" y="16" width="16" height="11" rx="3" fill="var(--teal-mid)"/><circle cx="14" cy="21.5" r="2.5" fill="var(--white)"/></svg>
        <span>555-314-8860</span>
      </div>
    </div>
  </main>
</body>
</html>
```